Kestrel Facilities Business Card Design

We would now like to design business cards with the new Kestrel Facilities logo

Target Market(s)

Professional

Industry/Entity Type

Professional services

Contact Information for Business Card

Employee name, title, phone number, email address, corporate office address and logo.

Font styles to use
Sans Serif

Colors
0054AA
0677BA
7BADD7
CADEEF
E8F1F8

Requirements
Must have
• My logo
Should not have
• any other pictures or images besides my logo

```html
<!DOCTYPE html>
<html lang="en">
<head>
<meta charset="utf-8">
<title>Kestrel Facilities Business Card</title>
<link href="https://fonts.googleapis.com/css2?family=Montserrat:wght@400;500;700;800&display=swap" rel="stylesheet">
<style>
  :root {
    --brand-blue: #3578be;
    --stripe-grey: #9d9d9f;
    --paper: #ffffff;
    --ink: #1d1d1f;
    --backdrop: #e3e4e6;
    --logo-light: #d8dde5;
  }
  * { margin: 0; padding: 0; box-sizing: border-box; }
  html, body {
    width: 1200px; height: 813px; overflow: hidden;
    background: var(--backdrop);
    font-family: "Montserrat", Arial, sans-serif;
  }
  .sheet {
    width: 1200px; height: 813px;
    display: flex; align-items: center; justify-content: center; gap: 40px;
  }
  .card {
    position: relative;
    width: 560px; height: 320px;
    border-radius: 22px;
    overflow: hidden;
    box-shadow: 0 6px 18px rgba(0,0,0,0.18);
  }
  .card-front { background: var(--paper); }
  .card-back { background: var(--brand-blue); display: flex; align-items: center; justify-content: center; }
  .front-waves { position: absolute; inset: 0; width: 100%; height: 100%; }
  .holder {
    position: absolute; left: 30px; top: 36px; color: var(--paper);
  }
  .holder-name {
    font-weight: 800; font-size: 24px; letter-spacing: 0.5px; text-transform: uppercase;
  }
  .holder-title { font-weight: 400; font-size: 16px; margin-top: 2px; }
  .contact {
    position: absolute; left: 60px; top: 190px; color: var(--ink);
    font-size: 13.5px; font-weight: 500; line-height: 1.35;
  }
  .contact-address { margin-bottom: 12px; }
  .contact-line { display: flex; align-items: center; gap: 8px; }
  .contact-icon { width: 14px; height: 14px; flex: none; }
  .front-brand {
    position: absolute; left: 320px; top: 165px; width: 220px;
    display: flex; align-items: center; gap: 12px;
    color: var(--brand-blue);
  }
  .brand-mark { width: 26px; height: 26px; background: var(--brand-blue); flex: none; }
  .brand-name { font-weight: 700; font-size: 26px; line-height: 1.05; }
  .back-brand {
    display: flex; align-items: center; gap: 16px; color: var(--logo-light);
  }
  .back-brand .brand-mark { width: 34px; height: 34px; background: var(--logo-light); }
  .back-brand .brand-name { font-size: 36px; }
</style>
</head>
<body>
<main class="sheet">
  <section class="card card-front">
    <svg class="front-waves" viewBox="0 0 560 320" aria-hidden="true">
      <defs>
        <path id="wave-line" d="M-10,136 C80,132 160,126 230,108 C300,88 350,48 400,30 C450,14 500,10 570,8"/>
      </defs>
      <path d="M0,0 H560 V8 C500,10 450,14 400,30 C350,48 300,88 230,108 C160,126 80,132 0,136 Z" fill="var(--brand-blue)"/>
      <use href="#wave-line" transform="translate(0,10)" fill="none" stroke="var(--stripe-grey)" stroke-width="6"/>
      <use href="#wave-line" transform="translate(0,20)" fill="none" stroke="var(--brand-blue)" stroke-width="5"/>
    </svg>

    <div class="holder">
      <p class="holder-name">Dana Whitfield</p>
      <p class="holder-title">Co-Founder</p>
    </div>

    <div class="contact">
      <p class="contact-address">1840 Harbor View Drive<br>Suite 410 Lakemont.12</p>
      <p class="contact-line">
        <svg class="contact-icon" viewBox="0 0 16 16" aria-hidden="true"><path d="M3 2 L6 2 L7 5 L5 6.5 C6 8.8 7.2 10 9.5 11 L11 9 L14 10 L14 13 C14 13.6 13.5 14 13 14 C7 14 2 9 2 3 C2 2.4 2.4 2 3 2 Z" fill="var(--brand-blue)"/></svg>
        +1-555-014-2276
      </p>
      <p class="contact-line">
        <svg class="contact-icon" viewBox="0 0 16 16" aria-hidden="true"><rect x="1" y="3" width="14" height="10" fill="var(--brand-blue)"/><path d="M1 3 L8 9 L15 3" fill="none" stroke="#fff" stroke-width="1.2"/></svg>
        info@kestrelfac.com
      </p>
      <p class="contact-line">
        <svg class="contact-icon" viewBox="0 0 16 16" aria-hidden="true"><circle cx="8" cy="8" r="7" fill="var(--brand-blue)"/><path d="M1 8 H15 M8 1 C5 4 5 12 8 15 M8 1 C11 4 11 12 8 15" fill="none" stroke="#fff" stroke-width="0.9"/></svg>
        www.kestrelfac.com
      </p>
    </div>

    <div class="front-brand">
      <span class="brand-mark"></span>
      <span class="brand-name">Kestrel<br>Facilities</span>
    </div>
  </section>

  <section class="card card-back">
    <div class="back-brand">
      <span class="brand-mark"></span>
      <span class="brand-name">Kestrel<br>Facilities</span>
    </div>
  </section>
</main>
</body>
</html>
```